Calvanto Group Real Estate Company business cards

New business card design, we are generally happy with the basic layout of the existing front of business card, (feel free to change) but require a head shot photo on the back side.

http://www.calvanto.com.au/

Attached logos, and existing business card

------------------------------

Target Market(s)

Real estate

Industry/Entity Type

Real Estate

Contact Information for Business Card

Standard size double sided

Font styles to use
Other font styles liked:
• Futura

Requirements
Must have
• Photo head shot on the back side
Nice to have
• yes
Should not have
• No

```html
<!DOCTYPE html>
<html lang="en">
<head>
<meta charset="utf-8">
<title>Calvanto Group – Business Cards</title>
<link href="https://fonts.googleapis.com/css2?family=PT+Sans:wght@400;700&display=swap" rel="stylesheet">
<style>
  :root {
    --page-bg: #eceae6;
    --card-dark: #1f2a34;
    --card-mid: #2d3a46;
    --accent-yellow: #f4d31f;
    --text-white: #ffffff;
    --brand-violet: #7268c9;
    --photo-navy: #1c2f52;
    --photo-blue: #3a4f7a;
  }
  * { box-sizing: border-box; margin: 0; padding: 0; }
  html, body {
    width: 1200px; height: 900px; overflow: hidden;
    background: var(--page-bg);
    font-family: "PT Sans", Arial, sans-serif;
  }
  .canvas { position: relative; width: 1200px; height: 900px; }
  .card {
    position: absolute;
    width: 556px; height: 342px;
    background: radial-gradient(ellipse at 45% 30%, var(--card-mid) 0%, var(--card-dark) 75%);
    box-shadow: 0 6px 18px rgba(0,0,0,0.25);
    color: var(--text-white);
    overflow: hidden;
  }
  .card--front { left: 238px; top: 62px; }
  .card--back  { left: 458px; top: 518px; width: 560px; }

  .brand-name {
    position: absolute;
    font-weight: 700;
    color: var(--brand-violet);
    white-space: nowrap;
    display: flex; align-items: center; gap: 8px;
  }
  .brand-name__dot { width: 10px; height: 10px; background: var(--brand-violet); }
  .card--front .brand-name { left: 48px; top: 150px; font-size: 30px; }
  .card--back .brand-name { left: 256px; top: 96px; font-size: 36px; }

  .details { position: absolute; left: 273px; top: 72px; }
  .details__name { font-size: 21px; font-weight: 700; color: var(--accent-yellow); }
  .details__role { font-size: 15px; margin-top: 2px; }
  .details__company { font-size: 18px; font-weight: 700; color: var(--accent-yellow); margin-top: 15px; }
  .details__abn { font-size: 15px; margin-top: 3px; }
  .details__abn b { font-weight: 700; }
  .contacts { list-style: none; margin-top: 22px; }
  .contacts li { display: flex; align-items: center; gap: 12px; font-size: 15px; height: 23.5px; }
  .contacts svg { width: 12px; height: 12px; fill: var(--accent-yellow); flex: none; }

  .headshot {
    position: absolute; left: 0; top: 0; width: 196px; height: 342px;
    background: linear-gradient(180deg, var(--card-mid) 0%, var(--photo-blue) 55%, var(--photo-navy) 100%);
  }
  .tagline {
    position: absolute; left: 196px; right: 0; text-align: center;
    font-weight: 700; color: var(--text-white);
  }
  .tagline--lead { top: 196px; font-size: 20px; left: 170px; right: 62px; }
  .tagline--services { top: 242px; font-size: 20px; left: 170px; right: 62px; word-spacing: 4px; }
</style>
</head>
<body>
<main class="canvas">
  <section class="card card--front">
    <div class="brand-name"><span class="brand-name__dot"></span>Calvanto Group</div>
    <div class="details">
      <p class="details__name">Marcus Tran</p>
      <p class="details__role">Director</p>
      <p class="details__company">Calvanto Group</p>
      <p class="details__abn"><b>ABN:</b> 47 215 608 934</p>
      <ul class="contacts">
        <li><svg viewBox="0 0 24 24"><path d="M6.6 10.8a15 15 0 0 0 6.6 6.6l2.2-2.2c.3-.3.7-.4 1-.2 1.1.4 2.3.6 3.6.6.6 0 1 .4 1 1V20c0 .6-.4 1-1 1A17 17 0 0 1 3 4c0-.6.4-1 1-1h3.5c.6 0 1 .4 1 1 0 1.3.2 2.5.6 3.6.1.3 0 .7-.2 1z"/></svg>0412 583 906</li>
        <li><svg viewBox="0 0 24 24"><path d="M2 5h20v14H2z M3 6l9 7 9-7" /><path d="M2 5l10 8 10-8v1l-10 8L2 6z" fill="#1f2a34"/></svg>marcus.tran@calvanto.com.au</li>
        <li><svg viewBox="0 0 24 24"><circle cx="12" cy="12" r="10"/><path d="M7 8c2 0 3 1 3 3s2 2 2 4-1 3-2 4M14 4c0 2 1 3 3 3s3 2 3 4" stroke="#1f2a34" stroke-width="1.6" fill="none"/></svg>www.calvanto.com.au</li>
      </ul>
    </div>
  </section>

  <section class="card card--back">
    <div class="headshot" role="img" aria-label="Head shot photo of the director in a navy suit and blue tie"></div>
    <div class="brand-name"><span class="brand-name__dot"></span>Calvanto Group</div>
    <p class="tagline tagline--lead">let us show you property</p>
    <p class="tagline tagline--services">Buy - Sell - Rent</p>
  </section>
</main>
</body>
</html>
```